Need Business Card for our Real Estate Business with Sales Executive's Picture

PANTONE 484 C ( RED)

PANTONE 2766 C ( BLUE

Industry/Entity Type

Real Estate

Contact Information for Business Card

Name, Mobile, email, & picture of Person
Agency Phone, address, Web address

Requirements
Must have
• Our Logo Colours, Agent Picture,

```html
<!DOCTYPE html>
<html lang="en">
<head>
<meta charset="UTF-8">
<title>Corvale Realty Business Card</title>
<link href="https://fonts.googleapis.com/css2?family=Open+Sans:ital,wght@0,400;0,600;1,700&display=swap" rel="stylesheet">
<style>
  :root {
    --backdrop: #3a3a3c;
    --card-black: #1e1e20;
    --card-black-soft: #262628;
    --brand-red: #a3302a;
    --brand-blue: #16245e;
    --ink-white: #ffffff;
    --ink-muted: #55555a;
  }
  * { margin: 0; padding: 0; box-sizing: border-box; }
  html, body {
    width: 799px; height: 1200px; overflow: hidden;
    background: var(--backdrop);
    font-family: "Open Sans", sans-serif;
  }
  .canvas { position: relative; width: 799px; height: 1200px; }

  .card {
    position: absolute; left: 80px; width: 640px; height: 366px;
    background: var(--card-black); overflow: hidden;
    box-shadow: 0 14px 30px rgba(0,0,0,.45);
  }
  .card-front { top: 100px; }
  .card-back { top: 700px; }

  /* front */
  .front-brand {
    position: absolute; left: 0; right: 0; top: 120px; text-align: center;
    font-size: 58px; font-weight: 600; letter-spacing: 10px;
    color: var(--ink-muted);
  }
  .front-web {
    position: absolute; left: 0; right: 0; bottom: 70px;
    display: flex; align-items: center; justify-content: center; gap: 18px;
    color: var(--ink-white); font-size: 17px; letter-spacing: .5px;
  }
  .front-web .rule { width: 60px; height: 3px; background: var(--brand-red); }

  /* back */
  .back-shapes { position: absolute; inset: 0; }
  .agent-name {
    position: absolute; left: 36px; top: 30px;
    color: var(--ink-white); font-size: 20px; font-weight: 700; font-style: italic;
  }
  .agent-title {
    position: absolute; left: 36px; top: 58px;
    color: var(--brand-red); font-size: 13px;
  }
  .brand-lockup {
    position: absolute; left: 360px; top: 118px;
    display: flex; align-items: center; gap: 12px;
  }
  .brand-mark { width: 12px; height: 12px; background: var(--brand-red); }
  .brand-name {
    color: var(--ink-white); font-size: 34px; font-weight: 600; letter-spacing: 6px;
  }
  .contact-list {
    position: absolute; left: 36px; top: 186px; list-style: none;
    color: var(--ink-white); font-size: 13px; line-height: 22px;
  }
  .contact-list li { display: flex; align-items: center; gap: 9px; }
  .contact-list svg { width: 12px; height: 12px; flex: none; }
  .contact-list .address { margin-left: -2px; }
  .agent-photo {
    position: absolute; left: 420px; top: 196px; width: 190px; height: 170px;
    background: linear-gradient(180deg, #3b2c26 0%, #9a6b50 40%, #223a86 75%, #1a2a66 100%);
    border-radius: 90px 90px 0 0;
  }
</style>
</head>
<body>
<main class="canvas">

  <section class="card card-front">
    <div class="front-brand">CORVALE</div>
    <div class="front-web">
      <span class="rule"></span>
      <span>www.corvalerealty.com</span>
      <span class="rule"></span>
    </div>
  </section>

  <section class="card card-back">
    <svg class="back-shapes" viewBox="0 0 640 366" width="640" height="366">
      <path d="M0,150 C120,118 205,160 265,228 C325,296 390,308 640,298 L640,366 L0,366 Z" fill="var(--brand-blue)"/>
      <path d="M0,140 C120,108 208,150 268,218 C328,286 392,296 640,288" fill="none" stroke="#111113" stroke-width="6"/>
      <path d="M0,128 C120,96 212,138 272,206 C332,274 394,282 640,274" fill="none" stroke="var(--brand-red)" stroke-width="8"/>
      <path d="M0,0 L0,60 C14,50 20,30 18,0 Z" fill="var(--brand-red)"/>
    </svg>

    <div class="agent-name">Dana Whitlock</div>
    <div class="agent-title">Managing Director</div>

    <div class="brand-lockup">
      <span class="brand-mark"></span>
      <span class="brand-name">CORVALE</span>
    </div>

    <ul class="contact-list">
      <li>
        <svg viewBox="0 0 12 12"><path d="M3 1 L5 3.5 L4 5 Q5 7 7 8 L8.5 7 L11 9 L9.5 11 Q4 10.5 1 3 Z" fill="#fff"/></svg>
        <span>555.010.2847</span>
      </li>
      <li>
        <svg viewBox="0 0 12 12"><rect x="3" y="0.5" width="6" height="11" rx="1.2" fill="#fff"/><rect x="4" y="2" width="4" height="6.5" fill="var(--brand-blue)"/></svg>
        <span>555-010-3391</span>
      </li>
      <li>
        <svg viewBox="0 0 12 12"><circle cx="6" cy="6" r="5" fill="none" stroke="#fff" stroke-width="1.2"/><ellipse cx="6" cy="6" rx="2.2" ry="5" fill="none" stroke="#fff" stroke-width="1"/><line x1="1" y1="6" x2="11" y2="6" stroke="#fff" stroke-width="1"/></svg>
        <span>corvalerealty.com</span>
      </li>
      <li>
        <svg viewBox="0 0 12 12"><rect x="0.5" y="2.5" width="11" height="7.5" fill="#fff"/><path d="M0.5 2.5 L6 7 L11.5 2.5" fill="none" stroke="var(--brand-blue)" stroke-width="1"/></svg>
        <span>dwhitlock@corvalerealty.com</span>
      </li>
      <li class="address"><span>48 Alder Row #210, Brookmont, CO 80000</span></li>
    </ul>

    <div class="agent-photo" role="img" aria-label="Portrait photo of the sales executive in a blue suit"></div>
  </section>

</main>
</body>
</html>
```